Website for a financial survey consultancy

WHO WE ARE
We're a niche HR consultancy specialising in salary comparison surveys for the financial asset management industry. We position ourselves as a small, highly responsive organisation with a strong personal relationship with each of our 50+ blue-chip clients.

WHAT WE DO
Our business is 80% surveys (= products), 20% consultancy (= services). The surveys are a set of online products which clients interact with to find the information they are interested in.

WHAT WE WANT
We are completely revising our existing marketing website and need a new up-to-date look and feel for the site. We want you to design 2 web pages
- Home page
- Internal content page

More details below in Must Have Priorities.

REFERENCE SITES
- www.veltramoor.com - nice background image
- www.plimweather.com - ignoring the animations
- www.gasketvale.com
- www.quorbin.com - clean, fresh, styly but prob not corporate enough
- www.dulveropinex.com - spacious, beautiful, slightly dated tho
- www.tambly.co.uk - ignore the colours. Like the simplicity, larger font size (although want to stick with sans-serif fonts for main content)

DELIVERABLES
The final designs should be delivered as one or more PSD files with clearly named layers. All design elements and treatments should be separated out, for example use adjustment layers rather than applied (and subsequently irreversible) adjustments, strokes, shading, etc.

WHAT NEXT
I'll be monitoring the contest every day and can respond to questions fast. You can IM me on Chatterlyne or QBX.

Reason: Hi folks,

I am extending the deadline to this project as I am travelling this week and therefore will not be able to make a final decision until next Monday. I will try and provide further feedback over the course of this week but I am only going to be online occasionally so be prepared to wait a few days for a reply from me.

Thanks for all the designs so far.

Tobias

Target Market(s)

In order of importance, most important first

1. Potential customers - UK & US financial industry HR professionals, short on time. Heard about us already, want to find out more about what we do, confirm relevance for their needs. Core goal - establish credibility: are we properly resourced, will we be around for years to come, are we *real*.

2. Existing customers - UK & US financial industry professionals, short on time, under pressure, want results quickly, minimum faff, expect high quality, slickly presented information. Primary action: login and use surveys.

3. Industry professionals/researchers - probably arriving through blog content, looking to browse and hoover information. Valuable for their ability to spread awareness of who we are amongst their peers.

Industry/Entity Type

Financial

Requirements
Must have
• GENERAL
Style cues - Corporate, professional, financial, stylish, slick, clean, spacious, light
Size - standard 960px grid

NAVIGATION
- [ Home | About us | Surveys | Consulting | Blog ]
- Sub-nav (roll-over dropdown) on About Us, Surveys & Consulting

ALL PAGES
- Site navigation
- Client login (on screen permanently or link to ajaxy in-page pop-up)
- Footer section
- Existing logo (attached)* - this is obviously an important reference point in the design, esp colour

HOME PAGE
- Communicate (link thru to?) survey/consulting split
- Large photo(s)/backdrop (2-3 interchangeable options ideally). Please consider what rights agreement will be necessary for any photos you include in your design.
- Possibly bigger more prominent version of logo
- Strap line/sentence - "Focussed data is the key to success"
- 3 recent blog posts (should look good with and without blog post images)
- Free downloadable PDF research report + supporting blurb

INTERNAL PAGE
- Page title
- Content - typical page will be less than one screenfull
- Level 1 sub-heading
- Level 2 sub-heading
- Bulleted list
- Content supporting image (any image will do - interested in placement, borders (if any), spacing, caption, etc)
- 'Do something' button

* Note: there is some internal debate about this logo at the moment. Some (me) are keen for it to change, some (not me!) are not. If you have an web page design idea/concept that requires an evolution of the logo, go ahead and evolve it. We can explore this further in the design process as necessary, but don't sweat it.
Nice to have
• Values to communicate
- Knowledgeable
- Professional
- Secure
- Personal
- Experienced
- Financial industry specific
- Accurate
- Reliable
Should not have
• - Search box
- Social media links, other than RSS feed button (discrete)

```html
<!DOCTYPE html>
<html lang="en">
<head>
<meta charset="utf-8">
<title>Norvale – Focussed data is the key to success</title>
<link rel="stylesheet" href="https://fonts.googleapis.com/css2?family=Tenor+Sans&family=Arimo:wght@400;700&display=swap">
<style>
  :root {
    --brand-red: #6b0a0a;
    --page-grey: #8f8d8d;
    --sky-top: #7fb6dc;
    --sky-mid: #a9cfe6;
    --haze: #d9dfe4;
    --panel-frame: rgba(170, 212, 238, 0.85);
    --panel-fill: rgba(160, 204, 230, 0.85);
    --tab-fill: #7fb1d6;
    --nav-fill: rgba(232, 232, 232, 0.88);
    --text-dark: #222;
    --text-body: #333;
    --rule: #b5b5b5;
    --white: #fff;
  }
  * { box-sizing: border-box; margin: 0; padding: 0; }
  html, body { width: 1200px; height: 750px; overflow: hidden; }
  body { background: var(--page-grey); font-family: "Arimo", Arial, sans-serif; }

  .page {
    position: absolute; left: 160px; top: 0; width: 900px; height: 750px;
    background: var(--white); box-shadow: 0 0 14px rgba(0,0,0,.45);
  }

  .hero { position: absolute; left: 0; top: 0; width: 900px; height: 562px; overflow: hidden; }
  .hero-backdrop {
    position: absolute; inset: 0;
    background: linear-gradient(180deg, var(--sky-top) 0%, var(--sky-mid) 55%, var(--haze) 85%, #c4cdd4 100%);
  }

  .brand-name {
    position: absolute; left: 26px; top: 44px;
    font-family: "Tenor Sans", sans-serif; color: var(--brand-red);
    font-size: 34px; line-height: 40px; letter-spacing: .5px;
  }

  .main-nav { position: absolute; left: 27px; top: 321px; width: 119px; list-style: none; }
  .main-nav li {
    height: 36px; margin-bottom: 1.5px; background: var(--nav-fill);
    font-family: "Tenor Sans", sans-serif; font-size: 13px; color: var(--brand-red);
    padding-left: 20px; line-height: 37px;
  }
  .main-nav li.is-current { background: var(--brand-red); color: var(--white); }

  .strapline { position: absolute; left: 186px; top: 72px; font-family: "Tenor Sans", sans-serif; font-weight: 400; }
  .strapline-main { display: block; color: var(--white); font-size: 50px; line-height: 54px; letter-spacing: .5px; }
  .strapline-sub { display: block; color: var(--brand-red); font-size: 36px; line-height: 38px; letter-spacing: 1.5px; margin-top: -4px; }

  .offer-panel {
    position: absolute; left: 488px; top: 267px; width: 392px; height: 244px;
    background: var(--panel-frame); padding: 8px;
  }
  .offer-inner { width: 100%; height: 100%; background: var(--panel-fill); position: relative; }
  .offer-tabs { display: flex; height: 50px; }
  .offer-tab {
    flex: 1; position: relative; padding: 8px 0 0 11px; color: var(--white);
    background: linear-gradient(180deg, #9ac4e2, var(--tab-fill));
  }
  .offer-tab + .offer-tab { border-left: 2px solid var(--panel-frame); background: linear-gradient(180deg, #8dbde0, #72a8d1); }
  .offer-tab-title { font-family: "Tenor Sans", sans-serif; font-size: 16px; display: block; }
  .offer-tab-sub { font-size: 11px; display: block; margin-top: 1px; }
  .offer-tab svg { position: absolute; right: 13px; top: 18px; }
  .offer-text {
    position: absolute; left: 12px; top: 66px; white-space: nowrap;
    font-size: 15.5px; line-height: 22.5px; color: var(--text-dark); letter-spacing: .2px;
  }
  .learn-button {
    position: absolute; left: 12px; top: 182px; width: 112px; height: 31px;
    background: linear-gradient(180deg, #c43030, var(--brand-red)); color: var(--white);
    font-size: 13.5px; line-height: 31px; padding-left: 10px; border-radius: 2px;
  }

  .footer-column { position: absolute; top: 580px; }
  .footer-heading { font-size: 15.5px; color: var(--brand-red); font-weight: 400; margin-bottom: 7px; }
  .footer-text { font-size: 11.5px; line-height: 15px; color: var(--text-body); }
  .learn-link { color: var(--brand-red); font-size: 10px; text-decoration: underline; }

  .blog-list { list-style: none; width: 253px; }
  .blog-list li { position: relative; padding: 0 0 8px 11px; border-bottom: 1px solid var(--rule); margin-bottom: 8px; }
  .blog-list li:last-child { border-bottom: 0; }
  .blog-list li::before {
    content: ""; position: absolute; left: 2px; top: 3px;
    border-left: 5px solid var(--brand-red); border-top: 4px solid transparent; border-bottom: 4px solid transparent;
  }

  .download-button {
    position: absolute; top: 102px; left: 0; width: 246px; height: 47px; border-radius: 3px;
    background: linear-gradient(180deg, #9ccbe8, #6fa7d0);
    color: var(--white); font-weight: 700; font-size: 16px; line-height: 15px; padding: 9px 0 0 58px;
  }
  .download-button .doc-icon { position: absolute; left: 6px; top: 4px; }

  .contact-block { line-height: 15px; }
  .copyright { font-size: 9.5px; color: var(--brand-red); margin-top: 25px; }

  .footer-name {
    position: absolute; left: 806px; top: 580px;
    font-family: "Tenor Sans", sans-serif; color: var(--brand-red); font-size: 20px; line-height: 24px;
  }
</style>
</head>
<body>
<div class="page">
  <header class="hero">
    <div class="hero-backdrop" role="img" aria-label="Photo of a suspension bridge with red cables over a city skyline under a blue sky"></div>

    <div class="brand-name">Norvale</div>

    <ul class="main-nav">
      <li class="is-current">HOME</li>
      <li>ABOUT US</li>
      <li>SURVEYS</li>
      <li>CONSULTING</li>
      <li>BLOG</li>
    </ul>

    <h1 class="strapline">
      <span class="strapline-main">FOCUSSED DATA</span>
      <span class="strapline-sub">is the key to success</span>
    </h1>

    <section class="offer-panel">
      <div class="offer-inner">
        <div class="offer-tabs">
          <div class="offer-tab">
            <span class="offer-tab-title">SURVEYS</span>
            <span class="offer-tab-sub">Aliquam erat volutpat.</span>
            <svg width="14" height="8" viewBox="0 0 14 8"><path d="M0 0h14L7 8z" fill="#fff"/></svg>
          </div>
          <div class="offer-tab">
            <span class="offer-tab-title">CONSULTING</span>
            <span class="offer-tab-sub">Aliquam erat volutpat.</span>
            <svg width="8" height="16" viewBox="0 0 8 16" style="top:13px"><path d="M0 0l8 8-8 8z" fill="#fff"/></svg>
          </div>
        </div>
        <p class="offer-text">Lorem ipsum dolor sit amet, consectetur<br>adipiscing elit. Morbi a purus vel sem<br>accumsan varius eget ut erat. Class aptent<br>taciti sociosqu ad litora torquent per conubia<br>nostra, per inceptos himenaeos.</p>
        <div class="learn-button">LEARN MORE</div>
      </div>
    </section>
  </header>

  <section class="footer-column" style="left:8px">
    <h2 class="footer-heading">BLOG</h2>
    <ul class="blog-list footer-text">
      <li>Lorem ipsum dolor sit amet, consectetur adipiscing elit. <span class="learn-link">LEARN MORE</span></li>
      <li>Morbi a purus vel sem accumsan varius eget ut erat. <span class="learn-link">LEARN MORE</span></li>
      <li>Class aptent taciti sociosqu ad litora torquent per conubia nostra. <span class="learn-link">LEARN MORE</span></li>
    </ul>
  </section>

  <section class="footer-column" style="left:299px; width:250px; height:150px">
    <h2 class="footer-heading">FREE Download</h2>
    <p class="footer-text" style="padding-left:2px">er inceptos himenaeos. Pellentesque habitant morbi tristique senectus et netus et malesuada fames ac turpis egestas. Aliquam erat volutpat. Maecenas dapibus</p>
    <div class="download-button">
      <svg class="doc-icon" width="44" height="40" viewBox="0 0 44 40">
        <rect x="4" y="1" width="36" height="38" rx="2" fill="#c62b23"/>
        <path d="M30 1v10h10" fill="#e9a6a0"/>
      </svg>
      RESEARCH REPORT +<br>SUPPORTING BLURB
    </div>
  </section>

  <section class="footer-column" style="left:572px">
    <h2 class="footer-heading">Contact Us</h2>
    <p class="footer-text contact-block" style="padding-left:2px">
      Norvale<br>
      Suite 200 - 845 Larkmoor Ave. N.W.<br>
      Cityname, State Name<br>
      USA<br><br>
      E-mail: contact@norvale.com
    </p>
    <p class="copyright">© 2011 Norvale.com. All rights reserved</p>
  </section>

  <div class="footer-name">Norvale</div>
</div>
</body>
</html>
```